Business Card Design Project

We are not a new company, but renamed to "Vantorin Kitchens" last year. We specialize in modern high-end cabinetry imports. We would like to communicate a sense of quality and cutting edge technology. Ideally the design would incorporate our logo colors, silver, red and preferably a black, matte background. Though we are open to suggestions.
Logo is attached.
Edit: I have attached rough drafts of the previous cards, this way you will have all necessary content that needs to go on the cards.
Updates
Project Deadline Extended
Reason: We have received a lot of great designs, but due to the sheer number we couldn't respond to all. We will extend the deadline for another 7 days to finalize and provide feedback to designers.
Thank you for your hard work!
Industry/Entity Type
Business
Look and feel
Each slider illustrates characteristics of the customer's brand and the style your logo design should communicate.

```html
<!DOCTYPE html>
<html lang="en">
<head>
<meta charset="utf-8">
<title>Vantorin Kitchens — Business Cards</title>
<link rel="stylesheet" href="https://fonts.googleapis.com/css2?family=Arimo:wght@400;700&display=swap">
<style>
  :root {
    --stage: #6e4a2f;
    --label: #1b1208;
    --card-black: #141414;
    --card-black-light: #2a2a2a;
    --silver: #c4c4c4;
    --silver-panel: #b9b9bb;
    --accent-red: #e0141b;
    --text-white: #f2f2f2;
  }
  * { margin: 0; padding: 0; box-sizing: border-box; }
  html, body { width: 1200px; height: 788px; overflow: hidden; }
  body {
    position: relative;
    background: var(--stage);
    font-family: "Arimo", Arial, sans-serif;
  }
  .label {
    position: absolute;
    width: 200px;
    text-align: center;
    font-size: 20px;
    color: var(--label);
  }
  .card {
    position: absolute;
    width: 525px;
    height: 300px;
    border-radius: 22px;
    overflow: hidden;
    background: radial-gradient(ellipse at 55% 40%, var(--card-black-light), var(--card-black) 75%);
    box-shadow: 0 4px 10px rgba(0,0,0,.45);
  }
  .card--back-alt { background: #050505; }
  .card__swoosh { position: absolute; inset: 0; }
  .holder {
    position: absolute;
    left: 24px;
    top: 26px;
    color: #fff;
  }
  .holder__name { font-size: 16px; font-weight: 700; line-height: 1.1; }
  .holder__name--light { font-weight: 400; }
  .holder__role { font-size: 14px; line-height: 1.3; }
  .brand {
    position: absolute;
    display: flex;
    align-items: center;
    gap: 12px;
    color: var(--silver);
    font-size: 27px;
    font-weight: 700;
    letter-spacing: 1px;
    white-space: nowrap;
  }
  .brand__square { width: 18px; height: 18px; background: var(--accent-red); }
  .brand--front { right: 22px; top: 124px; }
  .brand--back { left: 50%; top: 50%; transform: translate(-50%, -50%); font-size: 30px; }
  .contact {
    position: absolute;
    right: 20px;
    top: 206px;
    text-align: right;
    color: var(--text-white);
    font-size: 13.5px;
    line-height: 27px;
  }
  .pattern {
    position: absolute;
    background: radial-gradient(ellipse at center, #5a5a5a, #1a1a1a 60%, transparent 80%);
  }
  .pattern--top { left: 0; top: 0; width: 260px; height: 90px; }
  .pattern--bottom { right: 0; bottom: 0; width: 260px; height: 90px; }
</style>
</head>
<body>
  <div class="label" style="left:207px; top:22px;">front</div>
  <div class="label" style="left:787px; top:22px;">front-1</div>
  <div class="label" style="left:214px; top:406px;">back</div>
  <div class="label" style="left:782px; top:406px;">Back - 1</div>

  <section class="card" style="left:53px; top:74px;">
    <svg class="card__swoosh" viewBox="0 0 525 300" width="525" height="300">
      <path d="M0 0 H300 Q120 50 0 196 Z" fill="var(--silver-panel)"/>
      <path d="M300 0 Q120 50 0 196 V212 Q125 62 318 0 Z" fill="#000"/>
      <path d="M310 0 Q124 58 0 204 V232 Q132 76 340 0 Z" fill="var(--accent-red)"/>
    </svg>
    <div class="holder">
      <div class="holder__name">MIRA HALDEN</div>
      <div class="holder__role">President</div>
    </div>
    <div class="brand brand--front"><span class="brand__square"></span>VANTORIN KITCHENS</div>
    <div class="contact">
      <div>phone : 555.210.0147 | cell : 555.210.3382</div>
      <div>fax : 555.210.0193 | mira@vantorinkitchens.ca</div>
      <div>1820 - 47 Ave., Northvale, AB T0X 2K4</div>
    </div>
  </section>

  <section class="card" style="left:624px; top:74px;">
    <svg class="card__swoosh" viewBox="0 0 525 300" width="525" height="300">
      <path d="M0 0 H300 Q120 50 0 196 Z" fill="var(--silver-panel)"/>
      <path d="M300 0 Q120 50 0 196 V212 Q125 62 318 0 Z" fill="#000"/>
      <path d="M310 0 Q124 58 0 204 V232 Q132 76 340 0 Z" fill="var(--accent-red)"/>
    </svg>
    <div class="holder">
      <div class="holder__name holder__name--light">OREN HALDEN</div>
      <div class="holder__role">Director</div>
    </div>
    <div class="brand brand--front"><span class="brand__square"></span>VANTORIN KITCHENS</div>
    <div class="contact">
      <div>phone : 555.210.0147 | cell : 555.210.6624</div>
      <div>fax : 555.210.0193 | oren@vantorinkitchens.ca</div>
      <div>1820 - 47 Ave., Northvale, AB T0X 2K4</div>
    </div>
  </section>

  <section class="card" style="left:56px; top:446px;">
    <div class="brand brand--back"><span class="brand__square"></span>VANTORIN KITCHENS</div>
  </section>

  <section class="card card--back-alt" style="left:624px; top:446px;">
    <div class="pattern pattern--top" role="img" aria-label="Perforated metal texture in the top corner"></div>
    <div class="pattern pattern--bottom" role="img" aria-label="Perforated metal texture in the bottom corner"></div>
    <div class="brand brand--back"><span class="brand__square"></span>VANTORIN KITCHENS</div>
  </section>
</body>
</html>
```